Flyer for Yoga and IronPulse.

Just initial idea and open to creativity: I am thinking right half of flyer to be IronPulse info and left half to be Yoga info.
Feel free to add text as needed but would like following:
Basic text: ZenLoftVo $69/mo unlimited sessions.
ZenLoftVO.com
IronPulse: $99 intro session. Largest IronPulse in Texas.
IronPulseVO.com

Located North Riverside Houston (NRVO)
Address: 4817 Marlow Pkwy Houston, tx

Please submit any and all designs. Looking to get some great ideas!

Target Market(s)

Young professionals free spirited and fun atmosphere.

Colors
3176b5
85acd3
32a6d7
32b7a4
f59195
cde9f5
f04a50

Requirements
Must have
• Professional yet fun. Text should include:
ZenLoftVo and IronPulse Vo taking each a half of the page seperatly get still be identifiable as one. Want to show there is two options for either yoga or IronPulse or do both!
IronPulse Intro is $99 adm yoga intro is $69.
Nice to have
• Also visit www.ironpulsevo.com for more ideas and info.

```html
<!DOCTYPE html>
<html lang="en">
<head>
<meta charset="utf-8">
<title>IronPulse Vo &amp; ZenLoftVo Flyer</title>
<link href="https://fonts.googleapis.com/css2?family=Oswald:wght@400;500;600&display=swap" rel="stylesheet">
<style>
  :root{
    --red:#c1272d;
    --teal:#2cb6c8;
    --ink:#2e2e2e;
    --rule:#6b6b6b;
    --paper:#ffffff;
    --muted:#8a8a8a;
  }
  *{margin:0;padding:0;box-sizing:border-box}
  html,body{width:826px;height:1200px;overflow:hidden;background:var(--paper)}
  .flyer{position:relative;width:826px;height:1200px;background:var(--paper);font-family:"Oswald",sans-serif}
  .shapes{position:absolute;inset:0}
  .txt{position:absolute;text-transform:uppercase;white-space:nowrap}
  .site-top{left:44px;top:40px;font-size:31px;font-weight:500;color:#fff;letter-spacing:.5px}
  .site-bottom{right:48px;top:1044px;font-size:31px;font-weight:500;color:#fff;letter-spacing:.5px}

  .brand-gym{left:50px;top:274px;width:245px;text-align:center}
  .brand-gym .name{display:block;font-size:52px;font-weight:600;color:var(--red);line-height:1.02;letter-spacing:1px}
  .brand-gym .rule{display:block;height:1px;background:var(--muted);margin:12px 6px 6px}
  .brand-gym .place{display:block;font-size:8px;letter-spacing:2.5px;color:var(--ink)}

  .offer{display:block;color:var(--ink);font-weight:500;letter-spacing:.8px;line-height:1.35}
  .offer .price{color:var(--red);font-weight:600}
  .brand-gym .offer{font-size:15px;margin-top:14px}
  .brand-yoga .offer{font-size:15px;margin-top:12px}
  .brand-yoga .offer .price{color:var(--teal)}

  .brand-yoga{left:555px;top:650px;width:215px;text-align:center}
  .brand-yoga .dot{display:block;width:38px;height:38px;border-radius:50%;background:var(--teal);margin:0 auto 4px}
  .brand-yoga .rule{display:block;height:1px;background:var(--muted)}
  .brand-yoga .name{display:block;font-size:66px;font-weight:500;color:var(--red);line-height:.98;margin:8px 0 10px}
  .brand-yoga .place{display:block;font-size:11px;letter-spacing:2px;color:var(--ink);margin-bottom:12px}

  .cta{left:0;width:826px;top:1121px;text-align:center;font-size:22px;font-weight:500;color:var(--ink);letter-spacing:.3px}
  .address-band{position:absolute;left:0;bottom:0;width:826px;height:36px;background:var(--red);color:#fff;text-align:center;font-size:14px;line-height:36px;letter-spacing:.6px;text-transform:uppercase}
</style>
</head>
<body>
<div class="flyer">
  <svg class="shapes" width="826" height="1200" viewBox="0 0 826 1200">
    <defs>
      <linearGradient id="gymTone" x1="0" y1="0" x2="1" y2="1">
        <stop offset="0" stop-color="#8b8680"/>
        <stop offset=".5" stop-color="#5b5550"/>
        <stop offset="1" stop-color="#3a3634"/>
      </linearGradient>
      <linearGradient id="parkTone" x1="0" y1="0" x2="0" y2="1">
        <stop offset="0" stop-color="#dfe9ee"/>
        <stop offset=".35" stop-color="#a9b98f"/>
        <stop offset=".7" stop-color="#6c9a3c"/>
        <stop offset="1" stop-color="#4f8a2e"/>
      </linearGradient>
    </defs>
    <g role="img" aria-label="Photo: group training with kettlebells in a gym">
      <polygon points="330,15 811,15 811,453 330,557" fill="url(#gymTone)"/>
    </g>
    <polygon class="banner-top" points="15,15 631,15 15,163" fill="var(--red)"/>
    <line x1="15" y1="639" x2="811" y2="455" stroke="var(--rule)" stroke-width="6"/>
    <g role="img" aria-label="Photo: outdoor yoga class stretching on mats in a park">
      <polygon points="15,648 495,538 495,1092 15,1092" fill="url(#parkTone)"/>
    </g>
    <polygon class="banner-bottom" points="208,1107 811,966 811,1107" fill="var(--teal)"/>
  </svg>

  <div class="txt site-top">IronPulseVO.com</div>

  <div class="txt brand-gym">
    <span class="name">IronPulse<br>Vo</span>
    <span class="rule"></span>
    <span class="place">North Riverside Houston</span>
    <span class="offer"><span class="price">$99</span> Intro Session<br>Largest IronPulse in Texas</span>
  </div>

  <div class="txt brand-yoga">
    <span class="dot"></span>
    <span class="rule"></span>
    <span class="name">ZenLoft<br>Vo</span>
    <span class="place">North Riverside Houston</span>
    <span class="rule"></span>
    <span class="offer"><span class="price">$69/mo</span> Unlimited Sessions</span>
  </div>

  <div class="txt site-bottom">ZenLoftVO.com</div>

  <div class="txt cta">Visit us today for more information and follow us on Friendbook!</div>

  <div class="address-band">Located North Riverside Houston (NRVO) Address: 4817 Marlow Pkwy Houston, TX</div>
</div>
</body>
</html>
```